Looking for a modern, Professional business card design

We have a simple business card, but are looking for a more modern, professional look. A sample of the basic card is attached as well as the logo. We would also like to add that we offer:
Struggling with your finances?
- Learn to become debt free
- Discover the power of cash
- Control your money instead of it controlling you
Let us help you achieve a new level of financial freedom!
Also, we would like to have a "SPECIAL OFFER!: FREE 30 minute consultation"
Financial Planning

```html
<!DOCTYPE html>
<html lang="en">
<head>
<meta charset="utf-8">
<title>Summit Money Coaching – Business Card</title>
<link href="https://fonts.googleapis.com/css2?family=Open+Sans:wght@400;600;700;800&display=swap" rel="stylesheet">
<style>
  :root{
    --page:#e9e6df;
    --green-dark:#2f8a2a;
    --green:#4ba23a;
    --green-light:#9ccb45;
    --lime:#c5e06a;
    --ink:#1c1c1c;
    --grey:#4a4a4a;
    --white:#ffffff;
  }
  *{box-sizing:border-box;margin:0;padding:0}
  html,body{width:1200px;height:843px;overflow:hidden}
  body{background:var(--page);font-family:"Open Sans",Arial,sans-serif;position:relative}

  .card{position:absolute;top:262px;width:540px;height:318px;border-radius:22px;overflow:hidden;
        box-shadow:0 10px 28px rgba(0,0,0,.18)}
  .card--back{left:30px;background:var(--white)}
  .card--front{left:630px;background:linear-gradient(135deg,#6cb843 0%,var(--green) 45%,var(--green-dark) 100%)}

  /* back side */
  .back-mark{position:absolute;top:40px;left:0;right:0;display:flex;justify-content:center;align-items:center;gap:10px}
  .brand-dot{width:22px;height:22px;border-radius:50%;background:var(--green);flex:none}
  .brand-name{font-weight:800;font-size:22px;color:var(--green);letter-spacing:.5px;white-space:nowrap}
  .back-copy{position:absolute;top:112px;left:0;right:0;text-align:center}
  .back-copy__title{font-weight:800;font-size:19px;color:var(--green);letter-spacing:.3px}
  .back-copy__line{font-size:16px;color:var(--grey);line-height:22px}
  .back-offer{position:absolute;bottom:42px;left:0;right:0;text-align:center;font-weight:800;color:var(--green);font-size:20px}
  .back-offer span{font-size:19px;margin-left:8px}

  /* front side */
  .front-swoosh{position:absolute;inset:0;z-index:0}
  .front-person,.front-mark,.front-contact{z-index:1}
  .front-person{position:absolute;top:22px;right:28px;text-align:right;color:var(--white)}
  .front-person__name{font-size:21px;font-weight:400;line-height:28px}
  .front-person__role{font-size:16px;font-weight:400;line-height:22px}
  .front-mark{position:absolute;top:128px;left:112px;display:flex;align-items:center;gap:10px}
  .front-mark .brand-name{color:var(--ink);font-size:22px}
  .front-contact{position:absolute;left:36px;bottom:16px;color:var(--white);font-size:15px;line-height:26px}
  .front-contact__row{display:flex;align-items:center;gap:8px}
  .front-contact__row svg{width:15px;height:15px;flex:none}
  .front-contact__pair{display:flex;gap:22px}
</style>
</head>
<body>

<section class="card card--back" aria-label="Card back">
  <div class="back-mark">
    <span class="brand-dot"></span>
    <span class="brand-name">SUMMIT MONEY COACHING</span>
  </div>
  <div class="back-copy">
    <p class="back-copy__title">STRUGGLING WITH YOUR FINANCES?</p>
    <p class="back-copy__line">Learn to become debt free &bull; Discover the power of cash</p>
    <p class="back-copy__line">Control your money instead of it controlling you</p>
    <p class="back-copy__line">Let us help you achieve a new level of financial freedom!</p>
  </div>
  <p class="back-offer">SPECIAL OFFER!<span>FREE 30 minute consultation</span></p>
</section>

<section class="card card--front" aria-label="Card front">
  <svg class="front-swoosh" viewBox="0 0 540 318" preserveAspectRatio="none">
    <g transform="rotate(12 290 150)">
      <ellipse cx="290" cy="150" rx="290" ry="108" fill="none" stroke="var(--lime)" stroke-width="16" opacity=".5"/>
      <ellipse cx="290" cy="150" rx="266" ry="94" fill="none" stroke="var(--green-light)" stroke-width="8" opacity=".85"/>
      <ellipse cx="290" cy="150" rx="250" ry="80" fill="var(--white)"/>
    </g>
  </svg>
  <div class="front-person">
    <p class="front-person__name">Daniel R. Hayes</p>
    <p class="front-person__role">Personal Financial Coach</p>
  </div>
  <div class="front-mark">
    <span class="brand-dot"></span>
    <span class="brand-name">SUMMIT MONEY COACHING</span>
  </div>
  <div class="front-contact">
    <div class="front-contact__pair">
      <div class="front-contact__row">
        <svg viewBox="0 0 16 16"><rect x="4" y="1" width="8" height="14" rx="1.5" fill="none" stroke="#fff" stroke-width="1.5"/><circle cx="8" cy="12.5" r=".9" fill="#fff"/></svg>
        <span>(555) 014-2290</span>
      </div>
      <div class="front-contact__row">
        <svg viewBox="0 0 16 16"><rect x="1" y="3" width="14" height="10" fill="#fff"/><path d="M1 3l7 6 7-6" fill="none" stroke="var(--green)" stroke-width="1.3"/></svg>
        <span>daniel@summitmoneycoach.com</span>
      </div>
    </div>
    <div class="front-contact__row">
      <svg viewBox="0 0 16 16"><circle cx="8" cy="8" r="6.5" fill="none" stroke="#fff" stroke-width="1.4"/><ellipse cx="8" cy="8" rx="3" ry="6.5" fill="none" stroke="#fff" stroke-width="1.2"/><path d="M1.5 8h13" stroke="#fff" stroke-width="1.2"/></svg>
      <span>www.summitmoneycoach.com</span>
    </div>
  </div>
</section>

</body>
</html>
```